Appraisal and Umpire Services for Property Damage Insurance Claims

I need a banner design that I can post as an advertisement on industry web pages. I would like this to be elegant and reflective of quality, integrity and professionalism.

Target Market(s)

Insurance Companies and Attorneys

Industry/Entity Type

Insurance

Contact Information for Business Card

Gordon T. Ashby
218 Birchwell Lane
PO Box 913
Clifton Park, NY 12348
gashby@meridaleclaims.com
Phone: (800) 519-4867, Ext. 2716
Direct: (315) 648-9052

Logo Text

Line One: Silver Hollow Claim Service, Inc. Line two: Appraisal and Umpire Services

Font styles to use
Serif
Sans Serif

Colors
0255a3
f78f20
faa54b
3176b5

Requirements
Must have
• New Logo and matching banner, business card and stationary.
• The colors must be orange and navy blue in the logo. I have selected them below.

```html
<!DOCTYPE html>
<html lang="en">
<head>
<meta charset="utf-8">
<title>Silver Hollow Claim Service – Appraisal &amp; Umpire Services</title>
<link rel="stylesheet" href="https://fonts.googleapis.com/css2?family=Montserrat:wght@300;400;500;600;700&display=swap">
<style>
  :root {
    --navy: #1f3c7a;
    --navy-deep: #282b5c;
    --orange: #f78f20;
    --orange-light: #faa54b;
    --grey-text: #6d6f73;
    --rule: #9a9ca3;
    --white: #ffffff;
  }
  * { margin: 0; padding: 0; box-sizing: border-box; }
  html, body {
    width: 1200px;
    height: 2400px;
    overflow: hidden;
    background: var(--white);
  }
  .banner {
    position: relative;
    width: 1200px;
    height: 2400px;
    background: var(--white);
    font-family: "Montserrat", Arial, sans-serif;
    overflow: hidden;
  }
  .brand {
    position: absolute;
    top: 104px;
    left: 0;
    width: 1200px;
    text-align: center;
  }
  .brand-name {
    display: block;
    font-size: 100px;
    font-weight: 600;
    letter-spacing: 2px;
    color: var(--navy);
    line-height: 1;
  }
  .brand-sub {
    display: block;
    margin-top: 18px;
    font-size: 50px;
    font-weight: 400;
    letter-spacing: 6px;
    color: var(--grey-text);
    line-height: 1;
  }
  .hero-photo {
    position: absolute;
    top: 410px;
    left: 0;
    width: 1200px;
    height: 1010px;
    background:
      radial-gradient(ellipse at 70% 30%, rgba(240,240,236,0.7), transparent 55%),
      radial-gradient(ellipse at 20% 40%, rgba(120,100,80,0.55), transparent 50%),
      linear-gradient(160deg, #8a8274 0%, #c9c3b6 45%, #e3ddd2 75%, #b9b3a6 100%);
  }
  .hero-curve {
    position: absolute;
    top: 1050px;
    left: 0;
    width: 1200px;
    height: 400px;
  }
  .services {
    position: absolute;
    top: 1500px;
    left: 0;
    width: 1200px;
    height: 340px;
  }
  .accent-bar {
    position: absolute;
    left: 76px;
    top: 10px;
    width: 8px;
    height: 320px;
    background: linear-gradient(to bottom, var(--navy) 0 50%, var(--orange) 50% 100%);
  }
  .headline {
    position: absolute;
    left: 112px;
    top: 0;
    font-size: 88px;
    font-weight: 300;
    line-height: 104px;
    color: var(--navy);
  }
  .divider {
    position: absolute;
    left: 632px;
    top: 14px;
    width: 3px;
    height: 300px;
    background: var(--rule);
  }
  .service-list {
    position: absolute;
    left: 672px;
    top: 22px;
    list-style: none;
    font-size: 46px;
    font-weight: 400;
    letter-spacing: 1px;
    color: var(--navy);
    line-height: 56px;
  }
  .service-list li { margin-bottom: 40px; }
  .cta {
    position: absolute;
    left: 312px;
    top: 1900px;
    width: 576px;
    height: 120px;
    border-radius: 14px;
    background: linear-gradient(to bottom, var(--orange-light), var(--orange));
    color: var(--white);
    font-size: 64px;
    font-weight: 500;
    line-height: 120px;
    text-align: center;
    text-decoration: none;
  }
  .contact-band {
    position: absolute;
    left: 0;
    top: 2112px;
    width: 1200px;
    height: 288px;
    background: var(--navy-deep);
    color: var(--white);
    text-align: center;
    font-size: 92px;
    font-weight: 700;
    line-height: 288px;
    letter-spacing: 1px;
  }
</style>
</head>
<body>
  <main class="banner">
    <header class="brand">
      <span class="brand-name">SILVER HOLLOW</span>
      <span class="brand-sub">CLAIM SERVICE, INC</span>
    </header>

    <div class="hero-photo" role="img" aria-label="Aerial photograph of a coastal neighbourhood with houses destroyed by a hurricane, debris scattered across sand"></div>

    <svg class="hero-curve" viewBox="0 0 1200 400" aria-hidden="true">
      <path d="M0 340 Q600 280 1200 110 L1200 400 L0 400 Z" fill="#ffffff"/>
      <path d="M560 320 Q900 270 1200 110 L1200 200 Q900 335 560 320 Z" fill="#f78f20"/>
    </svg>

    <section class="services">
      <div class="accent-bar"></div>
      <h1 class="headline">Appraisal<br>&amp; Umpire<br>Services</h1>
      <div class="divider"></div>
      <ul class="service-list">
        <li>PROPERTY</li>
        <li>CASUALTY</li>
        <li>CLAIM<br>ADMINISTRATION</li>
      </ul>
    </section>

    <a class="cta" href="#">Learn More</a>

    <footer class="contact-band">1-800-519-4867</footer>
  </main>
</body>
</html>
```